Lumbra Ember Oven Kitchen (restaurant)

Restaurant with a cool vibe.
We need a refresh of existing site. Appealing to a hip crowd of 25 or older age bracket (mid price to high small town). Constant changes food and cocktail menu. A vibing atmosphere with jazz funk hip music.
Must be able to scale for any device… phone/mobile device super important.
Instagram: @Lumbra.Bexwell
Website: lumbrabexwell.example

Target Market(s)

25-55 age group

Number of Pages Required

1 page

Font styles to use
Sans Serif

Requirements
Must have
• Simple to navigate. Simplicity is the key to all sophistication.

Links/Buttons
Menu
Gift Cards
Reservations
Take Out
Contact Us
Should not have
• Please, nothing generic looking… no cookie cutter look. Originality

```html
<!DOCTYPE html>
<html lang="en">
<head>
<meta charset="utf-8">
<title>Lumbra Ember Oven Kitchen</title>
<link rel="stylesheet" href="https://fonts.googleapis.com/css2?family=Heebo:wght@400;500;700;800&family=Montserrat:ital,wght@0,400;0,600;0,700;1,400&family=Lobster&family=Playfair+Display:wght@400;700&display=swap">
<style>
:root{
  --yellow:#fdd22f;
  --olive:#b79b22;
  --dark:#1b1b1b;
  --darker:#141414;
  --ink:#111;
  --white:#fff;
  --muted:#a9a9a9;
  --wine:#7a1f1f;
}
*{margin:0;padding:0;box-sizing:border-box}
html,body{width:1200px;height:4501px;overflow:hidden;background:var(--dark)}
body{position:relative;font-family:'Montserrat',sans-serif;color:var(--white)}
.abs{position:absolute}
.center{text-align:center}
.photo{position:absolute}
.btn{position:absolute;display:flex;align-items:center;justify-content:center;font-family:'Heebo',sans-serif;font-weight:700;font-size:14px;border-radius:8px;text-transform:uppercase;letter-spacing:.2px}
.btn-yellow{background:var(--yellow);color:var(--ink)}
.btn-outline{border:2px solid var(--white);color:var(--white)}
.btn-outline-dark{border:2px solid var(--ink);color:var(--ink)}
.btn-white{background:var(--white);color:var(--yellow)}

.topbar{top:0;left:0;width:1200px;height:33px;background:var(--yellow);color:var(--ink);font-size:11px;font-weight:600}
.topbar .item{position:absolute;top:10px;display:flex;align-items:center;gap:6px}

.nav{top:33px;left:0;width:1200px;height:75px;background:rgba(20,20,20,.9);z-index:3}
.brand{position:absolute;left:60px;top:12px;line-height:1}
.brand .name{font-family:'Heebo',sans-serif;font-weight:700;font-size:36px;letter-spacing:3px;color:var(--white)}
.brand .tag{font-family:'Heebo',sans-serif;font-size:12px;margin-left:18px;color:var(--white)}
.menu{position:absolute;top:31px;font-family:'Heebo',sans-serif;font-size:13px;color:#ddd}
.menu.active{color:var(--yellow)}

.hero{top:33px;left:0;width:1200px;height:680px;background:radial-gradient(ellipse at 30% 80%,#8a5a2c 0%,#4b3424 35%,#1e1a17 70%)}
.hero-script{left:748px;top:275px;font-family:'Lobster',cursive;font-size:22px;color:var(--yellow)}
.hero-title{left:748px;top:298px;font-family:'Heebo',sans-serif;font-weight:700;font-size:58px;line-height:60px;color:var(--white)}
.hero-sub{left:748px;top:424px;font-style:italic;font-size:14px}
.arrow{position:absolute;width:40px;height:40px;border-radius:50%;background:rgba(0,0,0,.5);display:flex;align-items:center;justify-content:center}

.about{top:713px;left:0;width:1200px;height:772px;background:linear-gradient(180deg,#1a1a1a,#242220 60%,#1b1b1b)}
.h2{font-family:'Heebo',sans-serif;font-weight:500;font-size:30px}
.hl{color:var(--yellow)}

.menu-band{top:1485px;left:0;width:1200px;height:412px;background:var(--yellow)}
.label-bar{position:absolute;left:0;bottom:0;width:100%;height:56px;background:rgba(20,20,20,.8);display:flex;align-items:center;justify-content:center;font-family:'Heebo',sans-serif;font-weight:700;font-size:13px}

.dish-name{position:absolute;width:260px;font-family:'Heebo',sans-serif;font-size:17px;text-align:center}
.dish-text{position:absolute;width:230px;font-size:11px;font-style:italic;color:#cfcfcf;text-align:center;line-height:20px}

.gift-band{top:2755px;left:0;width:1200px;height:480px;background:linear-gradient(90deg,#f0c52a,#fdd22f 40%,#e9c12b);overflow:hidden}
.gift-card{left:391px;top:3127px;width:418px;height:206px;background:#fffaf0;border:2px solid #e7d6a6;z-index:5}
.gift-inner{position:absolute;inset:9px;border:1px solid #d9b968}

.form{left:596px;top:3529px;width:412px;height:267px;background:#2a2a2a}
.f-label{position:absolute;left:32px;font-size:11px;color:#ccc}
.field{position:absolute;left:28px;width:360px;height:35px;background:var(--white);border-radius:3px}

.follow{top:3948px;left:0;width:1200px;height:271px;background:var(--olive)}

.footer{top:4219px;left:0;width:1200px;height:282px;background:var(--darker)}
.f-head{position:absolute;top:49px;font-family:'Heebo',sans-serif;font-weight:700;font-size:16px}
.f-line{position:absolute;font-size:11px;color:#ddd}
.f-line b{font-weight:700;color:var(--white)}
</style>
</head>
<body>

<div class="abs topbar">
  <div class="item" style="left:868px">
    <svg width="14" height="14" viewBox="0 0 24 24"><path d="M6.6 10.8a15 15 0 0 0 6.6 6.6l2.2-2.2c.3-.3.7-.4 1-.2 1.1.4 2.3.6 3.6.6.6 0 1 .4 1 1V20c0 .6-.4 1-1 1A17 17 0 0 1 3 4c0-.6.4-1 1-1h3.5c.6 0 1 .4 1 1 0 1.3.2 2.5.6 3.6.1.3 0 .7-.2 1z" fill="#111"/></svg>
    555-014-2290
  </div>
  <div class="item" style="left:978px">
    <svg width="16" height="12" viewBox="0 0 16 12"><rect x="1" y="1" width="14" height="10" fill="none" stroke="#111" stroke-width="1.5"/><path d="M1 1l7 6 7-6" fill="none" stroke="#111" stroke-width="1.5"/></svg>
    hello@lumbrabexwell.example
  </div>
</div>

<div class="abs hero" role="img" aria-label="Close-up of wood-fired pizzas on a counter in front of the oven"></div>
<div class="abs" style="top:0;left:0;width:1200px;height:713px;background:linear-gradient(90deg,rgba(0,0,0,0) 40%,rgba(0,0,0,.45))"></div>
<svg class="abs" style="top:680px;left:0" width="1200" height="40" viewBox="0 0 1200 40" preserveAspectRatio="none"><path d="M0 20 L60 30 L120 18 L200 28 L280 15 L360 27 L440 20 L520 32 L600 18 L680 28 L760 16 L840 30 L920 20 L1000 28 L1080 16 L1150 26 L1200 14 L1200 40 L0 40Z" fill="#1a1a1a"/></svg>

<nav class="abs nav">
  <div class="brand"><div class="name">LUMBRA</div><div class="tag">Ember Oven Kitchen</div></div>
  <svg class="abs" style="left:555px;top:37px" width="6" height="6"><circle cx="3" cy="3" r="3" fill="#fdd22f"/></svg>
  <div class="menu active" style="left:572px">Home</div>
  <div class="menu" style="left:631px">Menu</div>
  <div class="menu" style="left:685px">Reservations</div>
  <div class="menu" style="left:783px">Order Online</div>
  <div class="menu" style="left:880px">Contact Us</div>
  <svg class="abs" style="left:964px;top:32px" width="15" height="15" viewBox="0 0 16 16"><circle cx="6.5" cy="6.5" r="5" fill="none" stroke="#ddd" stroke-width="1.6"/><path d="M10 10l5 5" stroke="#ddd" stroke-width="1.6"/></svg>
  <div class="btn" style="left:1001px;top:21px;width:136px;height:35px;border:2px solid var(--yellow);color:var(--yellow)">Order Online</div>
</nav>

<div class="abs hero-script">Lumbra Ember Oven Kitchen</div>
<div class="abs hero-title">Lets Get Lunch<br>At Lumbra !</div>
<div class="abs hero-sub">A vibing atmosphere with jazz funk hip music.</div>
<div class="btn btn-yellow" style="left:746px;top:466px;width:156px;height:39px">Order Online</div>
<div class="btn btn-outline" style="left:910px;top:466px;width:156px;height:39px">Book A Table</div>
<div class="arrow" style="left:60px;top:394px"><svg width="10" height="14"><path d="M8 1L2 7l6 6" fill="none" stroke="#fff" stroke-width="1.5"/></svg></div>
<div class="arrow" style="left:1098px;top:394px"><svg width="10" height="14"><path d="M2 1l6 6-6 6" fill="none" stroke="#fff" stroke-width="1.5"/></svg></div>

<section class="abs about" role="img" aria-label="Dim brick building facade behind the section"></section>
<div class="abs h2 center" style="top:783px;left:0;width:1200px">Lumbra Ember <span class="hl">Oven Kitchen</span></div>
<div class="abs center" style="top:830px;left:0;width:1200px;font-size:14px;font-style:italic">A vibing atmosphere with jazz funk hip music.</div>
<div class="abs center" style="top:866px;left:340px;width:520px;font-size:13px;font-style:italic;line-height:23px">Enjoy Some of the most Exquisite and Delicious Dishes. With our Unique Recipes we Guarantee a Taste you Won't Forget!</div>
<div class="abs center" style="top:920px;left:350px;width:500px;font-size:11px;color:var(--muted);line-height:19.5px">Lorem Ipsum has been the industry's standard dummy text ever since the 1500s, when an unknown printer took a galley of type and scrambled it to make a type specimen book. It has survived not only five centuries.</div>
<div class="photo" style="left:332px;top:996px;width:524px;height:489px;background:radial-gradient(ellipse at 50% 55%,#6b5446 0%,#3b302a 45%,rgba(30,28,26,0) 75%)" role="img" aria-label="Photo of the four owners smiling together"></div>
<div class="btn btn-yellow" style="left:531px;top:1001px;width:138px;height:34px">Order Online</div>

<section class="abs menu-band"></section>
<div class="photo" style="left:0;top:1600px;width:374px;height:388px;background:linear-gradient(160deg,#3a3a3a 0%,#6d5438 45%,#a4633a 75%,#5a3a22)" role="img" aria-label="Pizzas lined up in front of the wood-fired oven">
  <div class="label-bar">DINNER</div>
</div>
<div class="photo" style="left:840px;top:1432px;width:360px;height:374px;background:linear-gradient(150deg,#2a3340 0%,#6a4a22 45%,#d39a35 60%,#2a2a30)" role="img" aria-label="Two glasses of beer raised in a toast">
  <div class="label-bar">DRINK</div>
</div>
<div class="abs h2 center" style="top:1590px;left:400px;width:400px;color:var(--ink);font-weight:700;font-size:29px">Our Menu</div>
<div class="abs center" style="top:1639px;left:438px;width:324px;font-size:11.5px;color:#2a2a2a;line-height:20px">Lorem Ipsum has been the industry's standard dummy text ever since the 1500s, when an unknown printer took a galley</div>
<div class="btn btn-white" style="left:541px;top:1724px;width:118px;height:36px">Dinner</div>
<div class="btn btn-outline-dark" style="left:541px;top:1770px;width:118px;height:36px">Take Out</div>

<section class="abs" style="top:1897px;left:0;width:1200px;height:638px;background:linear-gradient(180deg,#1b1b1b,#242424 60%,#1b1b1b)"></section>
<div class="abs h2 center" style="top:2030px;left:0;width:1200px">Take <span class="hl">Out</span></div>
<div class="abs center" style="top:2076px;left:0;width:1200px;font-size:12px;font-style:italic;color:#ddd">Lorem Ipsum has been the industry's standard text ever since.</div>

<div class="photo" style="left:152px;top:2140px;width:220px;height:148px;background:radial-gradient(ellipse,#b8874f 0%,#8a6236 50%,rgba(27,27,27,0) 72%)" role="img" aria-label="Sandwich beside a kraft takeout box"></div>
<div class="dish-name" style="left:132px;top:2308px">Sandwiches</div>
<div class="dish-text" style="left:147px;top:2337px">Lorem Ipsum has been the industry's standard text ever since.</div>
<div class="btn btn-yellow" style="left:193px;top:2390px;width:140px;height:37px">Order Online</div>

<div class="photo" style="left:490px;top:2140px;width:220px;height:148px;background:radial-gradient(ellipse,#d0553a 0%,#a9683a 45%,rgba(27,27,27,0) 72%)" role="img" aria-label="Pizza with a kraft takeout box"></div>
<div class="dish-name" style="left:470px;top:2308px">Wood Fired Pizza</div>
<div class="dish-text" style="left:485px;top:2337px">Lorem Ipsum has been the industry's standard text ever since.</div>
<div class="btn btn-yellow" style="left:530px;top:2390px;width:140px;height:37px">Order Online</div>

<div class="photo" style="left:805px;top:2140px;width:220px;height:148px;background:radial-gradient(ellipse,#c98a44 0%,#7c6d34 45%,rgba(27,27,27,0) 72%)" role="img" aria-label="Burger next to a kraft takeout box"></div>
<div class="dish-name" style="left:785px;top:2308px">Burgers</div>
<div class="dish-text" style="left:800px;top:2337px">Lorem Ipsum has been the industry's standard text ever since.</div>
<div class="btn btn-yellow" style="left:845px;top:2390px;width:140px;height:37px">Order Online</div>

<section class="abs gift-band" role="img" aria-label="Brick building facade tinted yellow">
  <div class="abs" style="top:235px;left:770px;font-family:'Heebo',sans-serif;font-weight:800;font-size:78px;letter-spacing:4px;color:rgba(255,255,255,.14)">LUMBRA</div>
</section>

<div class="photo" style="left:253px;top:2535px;width:694px;height:388px;background:linear-gradient(160deg,#2b2824 0%,#5a4330 45%,#8a6a3e 70%,#3a2c20)" role="img" aria-label="Video still of burgers and fries at the bar">
  <svg class="abs" style="left:317px;top:164px" width="60" height="60" viewBox="0 0 60 60"><circle cx="30" cy="30" r="29" fill="rgba(255,255,255,.92)"/><path d="M24 18l18 12-18 12z" fill="#1b1b1b"/></svg>
</div>

<div class="abs center" style="top:2998px;left:0;width:1200px;font-family:'Montserrat',sans-serif;font-weight:700;font-size:28px;line-height:34px;color:var(--ink)">Order Online And Get<br><span style="color:var(--white);letter-spacing:2px">GIFT CARD</span></div>
<div class="abs center" style="top:3080px;left:0;width:1200px;font-size:11px;color:#333">Eat Healthy</div>

<section class="abs" style="top:3235px;left:0;width:1200px;height:713px;background:var(--dark)"></section>

<div class="abs gift-card">
  <div class="gift-inner"></div>
  <div class="photo" style="left:0;top:0;width:170px;height:202px;background:linear-gradient(135deg,#f4d270,#d9a628 55%,rgba(255,250,240,0) 80%)" role="img" aria-label="Gold ribbon bow on the card corner"></div>
  <div class="abs center" style="left:190px;top:38px;width:200px;font-family:'Playfair Display',serif;font-size:20px;color:var(--wine)">GIFT CARD</div>
  <div class="abs center" style="left:190px;top:78px;width:200px;font-family:'Playfair Display',serif;font-weight:700;font-size:48px;color:var(--wine)">30€</div>
  <div class="abs center" style="left:180px;top:155px;width:220px;font-family:'Playfair Display',serif;font-size:10px;color:var(--wine)">DISCOUNT CODE: <span style="color:#c79a2a">BEEI7C78Z</span></div>
</div>

<div class="abs center" style="top:3418px;left:597px;width:400px;font-family:'Montserrat',sans-serif;font-weight:700;font-size:28px;color:var(--yellow)">Reservations</div>
<div class="abs center" style="top:3466px;left:597px;width:400px;font-size:11px;color:#ddd;line-height:21px">Lorem Ipsum has been the industry's standard dummy text ever since the 1 an unknown printer took a galley</div>

<svg class="abs" style="left:129px;top:3730px" width="170" height="170"><circle cx="85" cy="85" r="85" fill="#5b4c16"/></svg>
<div class="photo" style="left:154px;top:3476px;width:363px;height:420px;border-radius:48% 48% 40% 40%;background:radial-gradient(ellipse at 50% 45%,#d6a56b 0%,#7a4a2a 45%,#3b2a1c 65%,rgba(27,27,27,0) 72%)" role="img" aria-label="Large roast beef sandwich on a ciabatta bun"></div>

<div class="abs form">
  <div class="f-label" style="top:26px">Date</div>
  <div class="field" style="top:44px"></div>
  <div class="f-label" style="top:101px">Time</div>
  <div class="field" style="top:117px"></div>
  <div class="f-label" style="top:178px">Party Size</div>
  <div class="field" style="top:196px"></div>
  <svg class="abs" style="left:38px;top:55px" width="14" height="14" viewBox="0 0 14 14"><rect x="1" y="2" width="12" height="11" rx="1" fill="none" stroke="#f3c94a" stroke-width="1.3"/><path d="M1 5h12" stroke="#f3c94a" stroke-width="1.3"/></svg>
  <svg class="abs" style="left:38px;top:128px" width="14" height="14" viewBox="0 0 14 14"><circle cx="7" cy="7" r="6" fill="none" stroke="#f3c94a" stroke-width="1.3"/><path d="M7 3.5V7l2.5 1.5" fill="none" stroke="#f3c94a" stroke-width="1.3"/></svg>
  <svg class="abs" style="left:38px;top:207px" width="14" height="14" viewBox="0 0 14 14"><circle cx="7" cy="5" r="3" fill="none" stroke="#f3c94a" stroke-width="1.3"/><path d="M1.5 13c1-3 3-4 5.5-4s4.5 1 5.5 4" fill="none" stroke="#f3c94a" stroke-width="1.3"/></svg>
  <svg class="abs" style="left:370px;top:60px" width="8" height="5"><path d="M0 0h8L4 5z" fill="#111"/></svg>
  <svg class="abs" style="left:370px;top:133px" width="8" height="5"><path d="M0 0h8L4 5z" fill="#111"/></svg>
  <svg class="abs" style="left:370px;top:212px" width="8" height="5"><path d="M0 0h8L4 5z" fill="#111"/></svg>
</div>
<div class="btn btn-yellow" style="left:723px;top:3774px;width:151px;height:38px">Find A Table</div>

<section class="abs follow"></section>
<div class="abs" style="top:4050px;left:61px;font-family:'Montserrat',sans-serif;font-weight:700;font-size:29px">Follow Us</div>
<div class="abs" style="top:4094px;left:61px;font-size:13px;font-style:italic;text-decoration:underline;color:var(--yellow)">#lumbra.bexwell</div>
<div class="photo" style="left:285px;top:4004px;width:166px;height:159px;background:linear-gradient(160deg,#7d8a8a,#8a4a42 60%,#4a3a30)" role="img" aria-label="Guests posing together on the patio"></div>
<div class="photo" style="left:456px;top:4004px;width:166px;height:159px;background:linear-gradient(160deg,#b8b2a0,#4a4440 55%,#5e6a70)" role="img" aria-label="Two friends standing outside"></div>
<div class="photo" style="left:629px;top:4004px;width:166px;height:159px;background:linear-gradient(160deg,#b0473c,#2c3a52 55%,#6a5a4a)" role="img" aria-label="Guest with a drink beside a shop sign"></div>
<div class="photo" style="left:800px;top:4004px;width:166px;height:159px;background:linear-gradient(160deg,#4a5a68,#c7a58e 55%,#7a3a3a)" role="img" aria-label="Two women at a dinner table"></div>
<div class="photo" style="left:973px;top:4004px;width:166px;height:159px;background:linear-gradient(160deg,#2a2a2a,#8a4a2a 55%,#d06a3a)" role="img" aria-label="Cook working in the kitchen"></div>

<footer class="abs footer">
  <div class="f-head" style="left:61px">Canada Day Hours!</div>
  <svg class="abs" style="left:61px;top:83px" width="14" height="14" viewBox="0 0 14 14"><circle cx="7" cy="7" r="6" fill="none" stroke="#fdd22f" stroke-width="1.3"/><path d="M7 3.5V7l2.5 1.5" fill="none" stroke="#fdd22f" stroke-width="1.3"/></svg>
  <div class="f-line" style="left:85px;top:83px">Thursday, July 1st &nbsp;- &nbsp;<b>Open</b></div>
  <div class="f-line" style="left:85px;top:107px">Friday, July 2nd &nbsp;- &nbsp;<b>Open</b></div>
  <div class="f-line" style="left:85px;top:131px">Saturday, July 3rd &nbsp;- &nbsp;<b>Open</b></div>
  <div class="f-line" style="left:85px;top:155px">Sunday, July 4th &nbsp;- &nbsp;<b>Closed</b></div>

  <div class="f-head" style="left:341px">Takeout &amp; Kitchen Hours</div>
  <svg class="abs" style="left:341px;top:83px" width="14" height="14" viewBox="0 0 14 14"><circle cx="7" cy="7" r="6" fill="none" stroke="#fdd22f" stroke-width="1.3"/><path d="M7 3.5V7l2.5 1.5" fill="none" stroke="#fdd22f" stroke-width="1.3"/></svg>
  <div class="f-line" style="left:372px;top:83px">Thursday to Sunday</div>
  <div class="f-line" style="left:372px;top:107px"><b>12:00pm - 8:00pm</b></div>

  <div class="f-head" style="left:631px">Outdoor Dining Hours</div>
  <svg class="abs" style="left:631px;top:83px" width="14" height="14" viewBox="0 0 14 14"><circle cx="7" cy="7" r="6" fill="none" stroke="#fdd22f" stroke-width="1.3"/><path d="M7 3.5V7l2.5 1.5" fill="none" stroke="#fdd22f" stroke-width="1.3"/></svg>
  <div class="f-line" style="left:655px;top:83px">Our courtyard is open!</div>
  <div class="f-line" style="left:655px;top:107px">Thursday to Sunday</div>
  <div class="f-line" style="left:655px;top:131px"><b>12:00pm - 9:00pm</b></div>

  <div class="abs" style="left:929px;top:40px;line-height:1">
    <div style="font-family:'Heebo',sans-serif;font-weight:700;font-size:36px;letter-spacing:3px">LUMBRA</div>
    <div style="font-family:'Heebo',sans-serif;font-size:12px;margin-left:20px">Ember Oven Kitchen</div>
  </div>
  <svg class="abs" style="left:942px;top:113px" width="13" height="13" viewBox="0 0 24 24"><path d="M6.6 10.8a15 15 0 0 0 6.6 6.6l2.2-2.2c.3-.3.7-.4 1-.2 1.1.4 2.3.6 3.6.6.6 0 1 .4 1 1V20c0 .6-.4 1-1 1A17 17 0 0 1 3 4c0-.6.4-1 1-1h3.5c.6 0 1 .4 1 1 0 1.3.2 2.5.6 3.6.1.3 0 .7-.2 1z" fill="#fdd22f"/></svg>
  <div class="f-line" style="left:968px;top:113px">555-014-2290</div>
  <svg class="abs" style="left:941px;top:139px" width="15" height="11" viewBox="0 0 16 12"><rect x="1" y="1" width="14" height="10" fill="none" stroke="#fdd22f" stroke-width="1.5"/><path d="M1 1l7 6 7-6" fill="none" stroke="#fdd22f" stroke-width="1.5"/></svg>
  <div class="f-line" style="left:968px;top:137px">hello@lumbrabexwell.example</div>
  <svg class="abs" style="left:940px;top:162px" width="36" height="14"><circle cx="7" cy="7" r="6" fill="none" stroke="#fdd22f" stroke-width="1.5"/><circle cx="27" cy="7" r="6" fill="none" stroke="#fdd22f" stroke-width="1.5"/></svg>

  <div class="abs center" style="left:0;top:253px;width:1200px;font-size:10px;color:#999"><span style="color:var(--yellow)">©LUMBRA</span> - 2021 All Rights Reserved</div>
</footer>

</body>
</html>
```